Business card design Needed for new logo / Construction business, home extensions and new builds

We need a business card design using our new logo files which i will attach to this project :)

We are a small construction business specialising in home extensions, new builds and property development. We are very ambitious and would appreciate professional and elegant designs for our new business card.

Very serious about using the services on MakerQuarry and recently acquired our new logo from here :)

Please get involved, i will feedback when i can as i am very busy but can respond daily, thanks

Target Market(s)

People that want to build onto their houses, new building developments or adding too their existing property

Industry/Entity Type

Construction

Contact Information for Business Card

Renwick Tolliver Construction, Lionel Ashby (Managing Director), Tel 07822254961, email - info@renwick-tolliver, www.renwick-tolliver.co.uk

Colors

Designer to choose colors to be used in the design.

Requirements
Must have
• I like a deep grey on the back please. A lot of you have provided black from and back, try mixing things up a little. The black looks cool 😎 Thanks

```html
<!DOCTYPE html>
<html lang="en">
<head>
<meta charset="utf-8">
<title>Renwick Tolliver Construction – Business Card</title>
<link href="https://fonts.googleapis.com/css2?family=Open+Sans:wght@400;600;700;800&display=swap" rel="stylesheet">
<style>
  :root {
    --backdrop: #232325;
    --card-front: #1e1e21;
    --card-back: #2a2a2e;
    --back-mark: #5a5a61;
    --gold: #e2a52b;
    --silver: #d3d4d7;
    --ink-light: #f4f4f4;
  }
  * { box-sizing: border-box; margin: 0; padding: 0; }
  html, body {
    width: 1200px; height: 780px; overflow: hidden;
    background: var(--backdrop);
    font-family: "Open Sans", Arial, sans-serif;
  }
  .canvas {
    width: 1200px; height: 780px;
    display: flex; justify-content: center; align-items: center; gap: 60px;
  }
  .card {
    width: 414px; height: 640px;
    border-radius: 26px;
    position: relative;
    box-shadow: 0 18px 40px rgba(0,0,0,0.55);
  }
  /* Back */
  .card--back {
    background: var(--card-back);
    display: flex; flex-direction: column; align-items: center; justify-content: center; gap: 18px;
  }
  .back-mark__square {
    width: 70px; height: 70px; background: var(--back-mark); border-radius: 6px;
  }
  .back-mark__name {
    color: var(--back-mark); font-weight: 700; font-size: 24px; letter-spacing: 2px;
    text-align: center; line-height: 1.3; text-transform: uppercase;
  }
  /* Front */
  .card--front {
    background: var(--card-front);
    display: flex; flex-direction: column; align-items: center;
    padding: 70px 28px 0;
  }
  .brand { display: flex; flex-direction: column; align-items: center; gap: 14px; }
  .brand__square { width: 46px; height: 46px; background: var(--gold); border-radius: 4px; }
  .brand__name {
    color: var(--gold); font-weight: 600; font-size: 19px; letter-spacing: 2.5px;
    text-transform: uppercase; text-align: center; line-height: 1.35;
  }
  .person { margin-top: 110px; text-align: center; }
  .person__name { font-weight: 800; font-size: 38px; line-height: 1.05; }
  .person__first { color: var(--silver); }
  .person__last { color: var(--gold); }
  .person__role { color: var(--ink-light); font-weight: 600; font-size: 15px; margin-top: 4px; }
  .icon-rule { display: block; margin-top: 14px; }
  .contact, .address {
    color: var(--ink-light); font-size: 15.5px; text-align: center; line-height: 1.5; margin-top: 8px;
  }
</style>
</head>
<body>
<main class="canvas">
  <section class="card card--back" aria-label="Card back">
    <div class="back-mark__square"></div>
    <p class="back-mark__name">Renwick Tolliver<br>Construction</p>
  </section>

  <section class="card card--front" aria-label="Card front">
    <div class="brand">
      <div class="brand__square"></div>
      <p class="brand__name">Renwick Tolliver<br>Construction</p>
    </div>

    <div class="person">
      <h1 class="person__name"><span class="person__first">Lionel</span> <span class="person__last">Ashby</span></h1>
      <p class="person__role">Managing Director</p>
    </div>

    <svg class="icon-rule" width="358" height="34" viewBox="0 0 358 34" aria-hidden="true">
      <g stroke="var(--gold)" stroke-width="1.5">
        <line x1="0" y1="17" x2="118" y2="17"/>
        <line x1="240" y1="17" x2="358" y2="17"/>
      </g>
      <g fill="var(--gold)">
        <circle cx="139" cy="17" r="15"/><circle cx="179" cy="17" r="15"/><circle cx="219" cy="17" r="15"/>
      </g>
      <g fill="none" stroke="#1e1e21" stroke-width="1.8" stroke-linecap="round" stroke-linejoin="round">
        <path d="M133 11c0 7 5 12 12 12l2-3-3-2-2 1c-2-1-4-3-5-5l1-2-2-3z"/>
        <rect x="171" y="11" width="16" height="12" rx="1"/><path d="M171 12l8 6 8-6"/>
        <circle cx="219" cy="17" r="8"/><path d="M211 17h16M219 9c-3 4-3 12 0 16M219 9c3 4 3 12 0 16"/>
      </g>
    </svg>

    <p class="contact">0782 225 4961<br>info@renwick-tolliver.co.uk<br>www.renwick-tolliver.co.uk</p>

    <svg class="icon-rule" width="358" height="34" viewBox="0 0 358 34" aria-hidden="true">
      <g stroke="var(--gold)" stroke-width="1.5">
        <line x1="0" y1="17" x2="158" y2="17"/>
        <line x1="200" y1="17" x2="358" y2="17"/>
      </g>
      <circle cx="179" cy="17" r="15" fill="var(--gold)"/>
      <g fill="none" stroke="#1e1e21" stroke-width="1.8" stroke-linejoin="round">
        <path d="M179 26c-5-6-7-9-7-12a7 7 0 0 1 14 0c0 3-2 6-7 12z"/><circle cx="179" cy="14" r="2.5"/>
      </g>
    </svg>

    <p class="address">Halden Road, Westmoor<br>Ashcombe, AC4 7QT</p>
  </section>
</main>
</body>
</html>
```